Title: Iron Ledger Sub: She never leaves the harbor - Book cover

I need a complete book cover, front, spine, and back.

Religions Book

This book is more about the Title so it should be strong and serious.

Like the color Deep Red and black, blue. Deep purple
Avoid greens, orange, yellows.

Maybe a picture of a strong hand on the Bible. OR someone yelling.

If any pictures are used they must be 100% royalty free with proof or a buyout of image.

I have attached a couple of designs that the client likes. Just as a reference. The exception they DIDN'T like the pictures in the book cover.

Please ask any questions to clarify.

Please see the file I just uploaded called 'Book Cover samples.png" The clients likes the Title: Salt and Ember" the best. Please create a design something closer to this. The like how the title jumps off the page with a 2D look.

Again the Title must standout, and any use of images must be a secondary to the design.

I am happy with we the designs that have been submitted so far.

I hope this helps you get closer.

Thank you

First of all I want to thank you for all of your designs. At the beginning the client thought he would like a picture that represented the title. But after looking at all of the designs. He has now decided NOT to have any pictures.

Here is what he wants

1. BOLD Font (San Serif only) no fancy versions for the Title "IRON LEDGER" in uppercase. The title font should have some dimension to it to appear 2D or 3D looks. Shiny look. It needs to looks like it jumping off the page.

2. The subtitle right below the title in San Serif font)

3. Background solid color either black, dark red, or dark blue. The background can be slightly textured or gradation fill, etc.

4. The cover must have a strong and bold statement.

Thank you again.

Please use this photo on the back cover.

Thank you

Requirements
Should not have
• A picture that over powers the Title.

```html
<!DOCTYPE html>
<html lang="en">
<head>
<meta charset="utf-8">
<title>Iron Ledger – Book Cover</title>
<link rel="stylesheet" href="https://fonts.googleapis.com/css2?family=Share+Tech+Mono&family=PT+Sans:wght@400&display=swap">
<style>
  :root {
    --navy-deep: #070b2c;
    --navy: #141a52;
    --glow: #f4f4f8;
    --glow-mid: #6a6e9c;
    --spine-light: #f2f2f4;
    --title-red: #6e0b0d;
    --title-red-dark: #2a0304;
    --author-ink: #101014;
  }
  html, body {
    margin: 0;
    padding: 0;
    width: 1200px;
    height: 864px;
    overflow: hidden;
    background: var(--navy-deep);
  }
  .cover-wrap {
    position: relative;
    width: 1200px;
    height: 864px;
    overflow: hidden;
  }
  .back-cover {
    position: absolute;
    left: 0; top: 0;
    width: 580px; height: 864px;
    background:
      radial-gradient(circle at 260px 820px, var(--glow) 0, #c9cadd 40px, var(--glow-mid) 170px, #2c3068 330px, rgba(20,26,82,0) 520px),
      linear-gradient(180deg, var(--navy-deep) 0%, var(--navy) 100%);
  }
  .spine {
    position: absolute;
    left: 580px; top: 0;
    width: 56px; height: 864px;
    background: linear-gradient(180deg, var(--spine-light) 0%, #d9dae6 30%, #6a6e9c 62%, #1a2058 82%, var(--navy-deep) 100%);
  }
  .spine-text {
    position: absolute;
    left: 8px;
    bottom: 22px;
    writing-mode: vertical-rl;
    transform: rotate(180deg);
    white-space: nowrap;
    color: var(--title-red);
    display: flex;
    align-items: center;
    gap: 14px;
  }
  .spine-author {
    font-family: "Share Tech Mono", monospace;
    font-size: 22px;
    letter-spacing: 7px;
    color: #b3161a;
  }
  .spine-title {
    font-family: "PT Sans", sans-serif;
    font-size: 34px;
    color: #b3161a;
    text-shadow: 2px -1px 0 var(--title-red-dark);
  }
  .front-cover {
    position: absolute;
    left: 636px; top: 0;
    width: 564px; height: 864px;
    background:
      radial-gradient(circle at 556px 20px, var(--glow) 0, #d6d7e4 50px, var(--glow-mid) 200px, #2c3068 360px, rgba(20,26,82,0) 560px),
      linear-gradient(180deg, var(--navy) 0%, var(--navy-deep) 100%);
  }
  .front-author {
    position: absolute;
    left: 145px; top: 66px;
    font-family: "Share Tech Mono", monospace;
    font-size: 46px;
    line-height: 64px;
    letter-spacing: 10px;
    color: var(--author-ink);
    text-shadow: 1px 2px 2px rgba(0,0,0,0.6), -1px -1px 0 rgba(255,255,255,0.15);
  }
  .front-author span { display: block; }
  .front-author .line-two { margin-left: -48px; }
  .front-title {
    position: absolute;
    left: 0; right: 0;
    top: 660px;
    text-align: center;
    font-family: "PT Sans", sans-serif;
    color: var(--title-red);
    text-shadow: 2px 2px 0 var(--title-red-dark), 3px 4px 6px rgba(0,0,0,0.6);
  }
  .front-title h1 {
    margin: 0;
    font-weight: 400;
    font-size: 74px;
    line-height: 80px;
    letter-spacing: 1px;
    margin-left: 30px;
  }
  .front-title p {
    margin: 18px 0 0 30px;
    font-size: 40px;
    line-height: 48px;
  }
</style>
</head>
<body>
  <div class="cover-wrap">
    <section class="back-cover" aria-label="Back cover"></section>

    <section class="spine" aria-label="Spine">
      <div class="spine-text">
        <span class="spine-author">MARTA QUELLEN</span>
        <span class="spine-title">Iron Ledger she never leaves the harbor</span>
      </div>
    </section>

    <section class="front-cover" aria-label="Front cover">
      <div class="front-author">
        <span class="line-one">MARTA</span>
        <span class="line-two">QUELLEN</span>
      </div>
      <div class="front-title">
        <h1>IRON LEDGER</h1>
        <p>she never leaves the harbor</p>
      </div>
    </section>
  </div>
</body>
</html>
```